Marta's Dwellings website

We need a simple website for our property investment business in the UK. We basically need our contact details and brief description.We have the company logo already done (via ArtFlockly) so please use these:https://drive.google.com/drive/folders/1szJ3iRhelElZ40NIFT7w-c14MaY3Y_oV?usp=sharingYou could use some stock photos of UK houses for now.Let me know when to provide more detailed descriptions, etc

Coding

Coded - Design and coding required

Number of Pages Required

1 page

Colors

Designer to choose colors to be used in the design.

```html
<!DOCTYPE html>
<html lang="en">
<head>
<meta charset="utf-8">
<title>Marta's Dwellings</title>
<link href="https://fonts.googleapis.com/css2?family=Catamaran:wght@500;700;800&family=Open+Sans:ital,wght@0,400;0,600;0,700;1,400&display=swap" rel="stylesheet">
<style>
:root{
  --ink:#1d1d1f;
  --dark:#1e1e21;
  --white:#ffffff;
  --muted:#3a3a3a;
  --line:#c9c9c9;
  --gold:#f5b400;
  --sky:#2a5fb0;
}
*{box-sizing:border-box;margin:0;padding:0}
html,body{width:1200px;height:3675px;overflow:hidden;background:var(--white)}
body{position:relative;font-family:"Open Sans",sans-serif;color:var(--ink)}
.abs{position:absolute}
.heading{font-family:"Catamaran",sans-serif;font-weight:700;letter-spacing:.5px}
.rule{position:absolute;height:3px;width:48px;background:var(--ink)}
.rule.light{background:var(--white)}

/* hero */
.hero{left:0;top:0;width:1200px;height:770px;overflow:hidden;
  background:linear-gradient(180deg,#1f4fa8 0%,#4f78b8 22%,#d79a5f 40%,#a86a3a 55%,#3b4a6b 75%,#20304f 100%)}
.brand{left:120px;top:80px;width:270px;text-align:center;color:var(--white);font-family:"Open Sans",sans-serif;font-weight:400;font-size:16px;letter-spacing:6px}
.brand-mark{left:232px;top:28px;width:46px;height:46px;border:3px solid var(--white)}
.enquire{left:928px;top:49px;width:129px;height:37px;border:2px solid var(--white);color:var(--white);font-weight:700;font-size:14px;display:flex;align-items:center;justify-content:center}
.nav{left:510px;top:118px;display:flex;gap:33px;color:var(--white);font-weight:700;font-size:15.5px}
.hero-title{left:0;width:1200px;top:290px;text-align:center;color:var(--white);font-family:"Open Sans",sans-serif;font-weight:700;font-size:76px}
.hero-sub{left:0;width:1200px;top:396px;text-align:center;color:var(--white);font-weight:600;font-size:25px;line-height:38px}
.cta{left:515px;top:490px;width:169px;height:48px;background:var(--white);color:var(--ink);font-weight:700;font-size:18px;display:flex;align-items:center;justify-content:center}
.arrow-btn{width:30px;height:30px;border-radius:50%;background:rgba(0,0,0,.45);display:flex;align-items:center;justify-content:center}
.hero-curve{left:0;top:640px}
.hero-badge{left:552px;top:670px;width:96px;height:96px;border-radius:50%;background:var(--white);box-shadow:0 4px 10px rgba(0,0,0,.25)}

/* about */
.about-photo{left:145px;top:852px;width:519px;height:415px;border:2px solid #e3e3e3;background:linear-gradient(160deg,#8a7a63 0%,#b9a27a 40%,#9dbde0 60%,#6d5a44 100%)}
.about-card{left:602px;top:903px;width:454px;height:313px;background:var(--white);box-shadow:0 2px 12px rgba(0,0,0,.18);padding:48px 42px}
.about-card h2{font-size:33px;line-height:38px}
.about-card p{margin-top:44px;font-size:13.5px;line-height:32px;color:var(--muted)}

/* why */
.why{left:0;top:1348px}
.why-title{left:0;width:1200px;top:1490px;text-align:center;color:var(--white);font-size:33px}
.feature{width:230px;text-align:center;color:var(--white);top:1619px}
.feature .icon{width:106px;height:106px;border-radius:50%;background:var(--white);border:3px solid #2a2a2a;margin:0 auto;outline:2px solid var(--white);display:flex;align-items:center;justify-content:center}
.feature h3{font-weight:600;font-size:16.5px;margin-top:20px}
.feature p{font-size:13px;line-height:25px;margin-top:4px}

/* dream */
.dream-title{left:0;width:1200px;top:1986px;text-align:center;font-size:33px}
.home-photo{height:272px;width:432px;top:2090px}
.home-card{top:2316px;width:408px;height:228px;background:var(--white);border:1px solid #d6d6d6;text-align:center;padding-top:20px}
.home-card h3{font-size:28px;line-height:34px}
.home-card .tag{font-weight:600;font-size:14px;margin-top:4px}
.home-card .price{font-size:15px;margin-top:2px}
.home-card .price b{font-weight:700}
.home-card p{font-size:12.5px;line-height:27px;margin:8px 22px 0}
.circle-arrow{width:36px;height:36px;border-radius:50%;background:#bdbdbd;display:flex;align-items:center;justify-content:center}

/* testimonial */
.testi{left:0;top:2636px;width:1200px;height:415px;background:linear-gradient(180deg,#232326,#1a1a1c)}
.testi-title{left:0;width:1200px;top:2706px;text-align:center;color:var(--white);font-size:33px}
.portrait{left:216px;top:2797px;width:183px;height:183px;border-radius:50%;background:linear-gradient(180deg,#8fa46c,#c3cfb4 60%,#7e8fa3)}
.quote{left:447px;top:2808px;width:560px;color:var(--white);font-style:italic;font-size:20px;line-height:37px}
.quote-by{left:447px;top:2929px;color:var(--white);font-size:19px;display:flex;align-items:center;gap:18px}

/* contact */
.contact-title{left:0;width:1200px;top:3124px;text-align:center;font-size:34px}
.col-label{font-size:21px;top:3234px}
.field{height:43px;border:1px solid #9a9a9a;border-radius:3px;font-size:13px;color:#555;padding-left:14px;display:flex;align-items:center}
.submit{left:568px;top:3489px;width:138px;height:40px;background:var(--ink);color:var(--white);font-weight:700;font-size:13px;display:flex;align-items:center;justify-content:center}
.info-icon{width:30px;height:30px;border-radius:50%;border:1px solid #777;display:flex;align-items:center;justify-content:center}
.info-text{font-size:13px;line-height:27px;color:var(--ink)}
.social{width:32px;height:32px;border-radius:50%;border:1px solid #777;top:3493px}
.footer-rule{left:148px;top:3603px;width:904px;height:1px;background:#9a9a9a}
.copyright{left:0;width:1200px;top:3630px;text-align:center;font-size:12.5px}
</style>
</head>
<body>

<!-- Hero -->
<section class="abs hero" role="img" aria-label="Photo of a city skyline at sunset with a bridge over the river"></section>
<div class="abs brand-mark"></div>
<div class="abs brand" style="top:116px">MARTA'S DWELLINGS</div>
<div class="abs enquire">ENQUIRE NOW</div>
<nav class="abs nav"><span>HOME</span><span>ABOUT US</span><span>OFFERS</span><span>WHY US</span><span>BLOGS</span><span>CONTACT</span></nav>
<h1 class="abs hero-title">Marta's Dwellings</h1>
<p class="abs hero-sub">Sed ut perspiciatis unde omnis iste natus dolor<br>voluptatem accusantium doloremque</p>
<div class="abs cta">GET STARTED</div>
<div class="abs arrow-btn" style="left:58px;top:401px"><svg width="12" height="14" viewBox="0 0 12 14"><path d="M8 2 3 7l5 5" stroke="#fff" stroke-width="2.4" fill="none"/></svg></div>
<div class="abs arrow-btn" style="left:1112px;top:401px"><svg width="12" height="14" viewBox="0 0 12 14"><path d="M4 2l5 5-5 5" stroke="#fff" stroke-width="2.4" fill="none"/></svg></div>
<svg class="abs hero-curve" width="1200" height="135" viewBox="0 0 1200 135">
  <path d="M0 131 Q300 80 560 70 L650 70 Q900 80 1160 125 L1200 125 L1200 135 L0 135Z" fill="#fff"/>
  <path d="M0 131 Q300 78 560 68" stroke="#111" stroke-width="6" fill="none"/>
  <path d="M650 68 Q900 80 1155 122" stroke="#111" stroke-width="8" fill="none"/>
</svg>
<div class="abs hero-badge"></div>

<!-- About -->
<div class="abs about-photo" role="img" aria-label="Photo of a historic stone high street with shoppers"></div>
<div class="abs about-card">
  <h2 class="heading">MARTA'S DWELLINGS</h2>
  <div class="rule" style="left:42px;top:100px"></div>
  <p>Sed ut perspiciatis unde omnis iste natus astror sitous voluptatem accusantium doloremque laudantium, selt totam rem aperiam, eaque ipsa quae ab illo inventore veritatis et quasi architecto beatae vitae</p>
</div>

<!-- Why -->
<svg class="abs why" width="1200" height="571" viewBox="0 0 1200 571">
  <path d="M0 0 L600 62 L1200 0 L1200 571 L0 571Z" fill="#1e1e21"/>
</svg>
<h2 class="abs heading why-title">WHY MARTA'S DWELLINGS</h2>
<div class="rule light" style="left:576px;top:1549px"></div>
<div class="abs" style="left:68px;top:1714px"><svg width="10" height="14" viewBox="0 0 10 14"><path d="M7 2 2 7l5 5" stroke="#fff" stroke-width="2" fill="none"/></svg></div>
<div class="abs" style="left:1126px;top:1714px"><svg width="10" height="14" viewBox="0 0 10 14"><path d="M3 2l5 5-5 5" stroke="#fff" stroke-width="2" fill="none"/></svg></div>

<div class="abs feature" style="left:125px">
  <div class="icon"><svg width="56" height="50" viewBox="0 0 56 50" fill="none" stroke="#111" stroke-width="2"><circle cx="28" cy="16" r="8"/><circle cx="12" cy="20" r="6"/><circle cx="44" cy="20" r="6"/><path d="M14 48v-10a14 14 0 0 1 28 0v10M2 46v-6a10 10 0 0 1 10-10M54 46v-6a10 10 0 0 0-10-10"/></svg></div>
  <h3>Open and free system</h3>
  <p>Sed ut perspiciatis unde omnis iste natus sit volupats atem accu santium dolor</p>
</div>
<div class="abs feature" style="left:366px">
  <div class="icon"><svg width="54" height="54" viewBox="0 0 54 54" fill="none" stroke="#111" stroke-width="2"><circle cx="25" cy="29" r="20"/><ellipse cx="25" cy="29" rx="9" ry="20"/><path d="M5 29h40M8 19h34M8 39h34M40 6l10 10M45 4l-3 14"/></svg></div>
  <h3>Strategic location</h3>
  <p>Sed ut perspiciatis unde omnis iste natus sit volupats atem accu santium dolor</p>
</div>
<div class="abs feature" style="left:600px">
  <div class="icon"><svg width="56" height="54" viewBox="0 0 56 54" fill="none" stroke="#111" stroke-width="2"><circle cx="32" cy="14" r="10"/><path d="M32 8v12M29 11h5a2 2 0 0 1 0 4h-4a2 2 0 0 0 0 4h5M4 40l12-10h14a3 3 0 0 1 0 6H22M30 36l16-8a3 3 0 0 1 3 5L28 48H12"/></svg></div>
  <h3>Convenient payment</h3>
  <p>Sed ut perspiciatis unde omnis iste natus sit volupats atem accu santium dolor</p>
</div>
<div class="abs feature" style="left:841px">
  <div class="icon"><svg width="50" height="50" viewBox="0 0 50 50" fill="none" stroke="#111" stroke-width="2"><rect x="8" y="14" width="20" height="32"/><rect x="28" y="4" width="14" height="42"/><path d="M2 46h46M13 20h4M19 20h4M13 28h4M19 28h4M13 36h4M19 36h4M33 12h4M33 20h4M33 28h4M33 36h4"/></svg></div>
  <h3>World-class infrastructure</h3>
  <p>Sed ut perspiciatis unde omnis iste natus sit volupats atem accu santium dolor</p>
</div>

<!-- Dream homes -->
<h2 class="abs heading dream-title">DREAM HOME WITH MARTA</h2>
<div class="rule" style="left:576px;top:2045px"></div>
<div class="abs circle-arrow" style="left:53px;top:2312px"><svg width="16" height="16" viewBox="0 0 16 16"><path d="M8 3 3 8l5 5M3 8h10" stroke="#fff" stroke-width="2.2" fill="none"/></svg></div>
<div class="abs circle-arrow" style="left:1113px;top:2312px"><svg width="16" height="16" viewBox="0 0 16 16"><path d="M8 3l5 5-5 5M13 8H3" stroke="#fff" stroke-width="2.2" fill="none"/></svg></div>

<div class="abs home-photo" style="left:143px" role="img" aria-label="Photo of a brick family house covered in greenery"></div>
<style>.home-photo{background:linear-gradient(180deg,#4f86c9 0%,#7a9f6a 35%,#5e7a3e 70%,#8a8a7a 100%)}</style>
<div class="abs home-card" style="left:156px">
  <h3 class="heading">OUR RESIDENCES</h3>
  <div class="tag">Luxury 1-Bedroom apartments in UK</div>
  <div class="price">from <b>$ 21,000*</b></div>
  <p>Breathtaking views of the UK | Elegant lobby with 24-hour reception and concierge desk | Landscaped gardens | Temperature-controlled swimming pool</p>
</div>

<div class="abs home-photo" style="left:624px;background:linear-gradient(180deg,#8fb6e6 0%,#c7d8ea 30%,#9a4a32 55%,#7a6a5c 100%)" role="img" aria-label="Photo of a red brick detached villa with a garage"></div>
<div class="abs home-card" style="left:636px">
  <h3 class="heading">JUST VILLAS</h3>
  <div class="tag">Designer villas with interiors in UK</div>
  <div class="price">from <b>$ 21,000*</b></div>
  <p>Stunning views of UK | &nbsp;Fully equipped kitchen | In-room per sonalised service | Concierge | Kids Club | 24-hour restaurant | Health club and spa</p>
</div>

<!-- Testimonial -->
<section class="abs testi"></section>
<h2 class="abs heading testi-title">WHAT INVESTORS ARE SAYING</h2>
<div class="rule light" style="left:576px;top:2768px"></div>
<div class="abs portrait" role="img" aria-label="Portrait photo of a smiling investor outdoors"></div>
<p class="abs quote">“ Sed usat perspiciatis unde omnis iste natus asoror sit volupt atemas accusantium doloremqueu laudantium, nemo enim ipsam voluptatem quia voluptas aspernatur. ”</p>
<div class="abs quote-by"><span>- LOREM IPSUM.</span>
  <svg width="118" height="20" viewBox="0 0 118 20" fill="#f5b400">
    <path id="st" d="M10 1l2.6 6 6.4.5-4.9 4.2 1.5 6.3L10 14.7 4.4 18l1.5-6.3L1 7.5l6.4-.5z"/>
    <use href="#st" x="24"/><use href="#st" x="48"/><use href="#st" x="72"/><use href="#st" x="96"/>
  </svg>
</div>

<!-- Contact -->
<h2 class="abs heading contact-title">CONTACT US</h2>
<div class="rule" style="left:576px;top:3182px"></div>
<div class="abs col-label" style="left:142px">Contact form</div>
<div class="abs col-label" style="left:766px">Contact Information</div>

<div class="abs field" style="left:144px;top:3285px;width:277px">First Name</div>
<div class="abs field" style="left:430px;top:3285px;width:276px">Last Name</div>
<div class="abs field" style="left:144px;top:3351px;width:277px">Email</div>
<div class="abs field" style="left:430px;top:3351px;width:276px">Phone No</div>
<div class="abs field" style="left:144px;top:3416px;width:562px;justify-content:space-between;padding-right:16px">Location
  <svg width="10" height="6" viewBox="0 0 10 6"><path d="M1 1l4 4 4-4" stroke="#555" stroke-width="1.3" fill="none"/></svg></div>
<div class="abs submit">SUBMIT NOW</div>

<div class="abs info-icon" style="left:768px;top:3278px"><svg width="12" height="16" viewBox="0 0 12 16"><path d="M6 15S1 9 1 6a5 5 0 0 1 10 0c0 3-5 9-5 9z" fill="#111"/><circle cx="6" cy="6" r="2" fill="#fff"/></svg></div>
<div class="abs info-text" style="left:814px;top:3278px">Unit 7, Orchard Court, 14-16 Willow Row,<br>Ashby Vale, Leicestershire,<br>United Kingdom, LE9 4QT.</div>
<div class="abs info-icon" style="left:768px;top:3379px"><svg width="14" height="14" viewBox="0 0 14 14"><path d="M3 1l3 3-2 2a8 8 0 0 0 4 4l2-2 3 3-2 2C6 13 1 8 1 3z" fill="#111"/></svg></div>
<div class="abs info-text" style="left:814px;top:3381px">+44 116 555 0142</div>
<div class="abs info-icon" style="left:768px;top:3434px"><svg width="14" height="11" viewBox="0 0 14 11"><rect x="0" y="0" width="14" height="11" rx="1" fill="#111"/><path d="M1 1l6 5 6-5" stroke="#fff" stroke-width="1.2" fill="none"/></svg></div>
<div class="abs info-text" style="left:814px;top:3436px">info@martasdwellings.example</div>
<div class="abs social" style="left:764px"></div>
<div class="abs social" style="left:815px"></div>
<div class="abs social" style="left:866px"></div>

<div class="abs footer-rule"></div>
<div class="abs copyright">Copyright © 2019. &nbsp;All rights reserved.</div>

</body>
</html>
```